Maple Gable Business Card

Colors can be blue, grey and white as you see in the attached logo. Needs to have a spot for name, title, phone, email, address, and website. There also needs to be a spot for an agent's picture.

Contact Information for Business Card

See project description.

Colors

Designer to choose colors to be used in the design.

```html
<!DOCTYPE html>
<html lang="en">
<head>
<meta charset="UTF-8">
<title>Maple Gable Business Card</title>
<link href="https://fonts.googleapis.com/css2?family=Montserrat:wght@400;500;600&display=swap" rel="stylesheet">
<style>
  :root {
    --backdrop: #2c2c2d;
    --card-grey: #58595b;
    --brand-blue: #2a7fc1;
    --brand-blue-deep: #1f6bb0;
    --paper: #ffffff;
    --photo-tint: #f1f1f1;
    --ink: #4a4a4a;
    --logo-grey: #8a8b8d;
  }
  * { margin: 0; padding: 0; box-sizing: border-box; }
  html, body { width: 1200px; height: 900px; overflow: hidden; }
  body {
    background: var(--backdrop);
    font-family: "Montserrat", sans-serif;
    display: flex;
    flex-direction: column;
    align-items: center;
    justify-content: center;
    gap: 40px;
  }
  .card {
    position: relative;
    width: 700px;
    height: 400px;
    overflow: hidden;
  }
  .card-front { background: var(--paper); }
  .card-shapes { position: absolute; inset: 0; }
  .agent-photo {
    position: absolute;
    left: 40px; top: 228px;
    width: 140px; height: 140px;
    background: var(--photo-tint);
  }
  .agent-name {
    position: absolute;
    left: 300px; top: 124px;
    color: var(--brand-blue-deep);
    font-weight: 600;
    font-size: 26px;
    letter-spacing: 0.5px;
    white-space: nowrap;
  }
  .agent-title {
    position: absolute;
    left: 330px; top: 160px;
    color: var(--ink);
    font-size: 16px;
  }
  .contact-list {
    position: absolute;
    left: 40px; top: 114px;
    list-style: none;
    color: var(--ink);
    font-size: 16px;
    line-height: 30px;
  }
  .contact-list li { display: flex; align-items: center; gap: 10px; }
  .contact-icon { width: 13px; height: 13px; fill: var(--brand-blue); flex: none; }
  .office-address {
    position: absolute;
    right: 110px; bottom: 34px;
    text-align: right;
    color: var(--ink);
    font-size: 18px;
    line-height: 28px;
    font-style: normal;
  }
  .card-back {
    background: var(--card-grey);
    display: flex;
    align-items: center;
    justify-content: center;
    gap: 14px;
  }
  .brand-mark {
    width: 22px; height: 22px;
    background: var(--logo-grey);
  }
  .brand-name {
    color: var(--logo-grey);
    font-weight: 500;
    font-size: 40px;
    letter-spacing: 3px;
    text-transform: uppercase;
  }
</style>
</head>
<body>
  <section class="card card-front" aria-label="Business card front">
    <svg class="card-shapes" viewBox="0 0 700 400" width="700" height="400" aria-hidden="true">
      <polygon points="30,0 700,0 700,400 652,400 572,26" fill="var(--card-grey)"/>
      <polygon points="0,10 530,58 618,400 652,400 572,26 30,0" fill="var(--brand-blue)"/>
      <line x1="40" y1="95" x2="522" y2="95" stroke="var(--brand-blue)" stroke-width="1.5"/>
    </svg>
    <div class="agent-photo" role="img" aria-label="Agent portrait photo"></div>
    <div class="agent-name">DANIEL REYES</div>
    <div class="agent-title">Director</div>
    <ul class="contact-list">
      <li><svg class="contact-icon" viewBox="0 0 24 24"><path d="M6.6 10.8a15 15 0 0 0 6.6 6.6l2.2-2.2a1 1 0 0 1 1-.25 11.4 11.4 0 0 0 3.6.57 1 1 0 0 1 1 1V20a1 1 0 0 1-1 1A17 17 0 0 1 3 4a1 1 0 0 1 1-1h3.5a1 1 0 0 1 1 1c0 1.25.2 2.45.57 3.57a1 1 0 0 1-.25 1z"/></svg>555 218-4407</li>
      <li><svg class="contact-icon" viewBox="0 0 24 24"><path d="M2 5h20v14H2zm2 2v.5l8 5 8-5V7z"/></svg>info@maplegable.com</li>
      <li><svg class="contact-icon" viewBox="0 0 24 24"><circle cx="12" cy="12" r="10"/></svg>www.maplegable.com</li>
    </ul>
    <address class="office-address">48 Alder Lane<br>Lowell, MA 01852</address>
  </section>

  <section class="card card-back" aria-label="Business card back">
    <span class="brand-mark"></span>
    <span class="brand-name">Maple Gable</span>
  </section>
</body>
</html>
```